Business Card for: Bramwell Financial Advisory Services Inc.

provide strategic financial advisory services to companies in the areas of corporate finance, mergers and acquisitions, executive coaching and strategic planning

Target Market(s)

Companies, banks, accountants, lawyers

Industry/Entity Type

High end business consulting in corporate finance, mergers and acquisitions, consulting

Contact Information for Business Card

Name of company, Name: xxxxxx xxxxxx , CEO, - phone number: 1-xxx-xxx-xxxx, - email address,

Requirements
Must have
• Must be professional and simple.
Nice to have
• simple, straight graphics, must give the impression that we are trustworthy, professional, competent
Should not have
• loud colors, loud design features

```html
<!DOCTYPE html>
<html lang="en">
<head>
<meta charset="utf-8">
<title>Bramwell Financial Advisory Inc. – Business Card</title>
<link href="https://fonts.googleapis.com/css2?family=Michroma&family=Roboto:wght@400&display=swap" rel="stylesheet">
<style>
  :root {
    --backdrop: #2b2b2b;
    --card-black: #151515;
    --accent-gold: #f9ae22;
    --paper-white: #ffffff;
    --rule-grey: #8a8a8a;
  }
  html, body {
    margin: 0;
    width: 1200px;
    height: 800px;
    overflow: hidden;
    background: var(--backdrop);
  }
  .canvas {
    position: relative;
    width: 1200px;
    height: 800px;
  }
  .business-card {
    position: absolute;
    left: 150px;
    top: 143px;
    width: 900px;
    height: 514px;
    background: var(--card-black);
    border-radius: 30px;
    overflow: hidden;
  }
  .card-swoosh {
    position: absolute;
    inset: 0;
    width: 900px;
    height: 514px;
  }
  .company-name {
    position: absolute;
    left: 70px;
    top: 200px;
    width: 330px;
    margin: 0;
    font-family: "Michroma", sans-serif;
    font-weight: 400;
    font-size: 26px;
    line-height: 1.45;
    letter-spacing: 1px;
    color: var(--paper-white);
    text-transform: uppercase;
  }
  .company-name .line { display: block; }
  .divider {
    position: absolute;
    left: 440px;
    top: 120px;
    width: 1px;
    height: 210px;
    background: var(--rule-grey);
  }
  .contact-block {
    position: absolute;
    left: 478px;
    top: 128px;
  }
  .person-name {
    margin: 0;
    font-family: "Michroma", sans-serif;
    font-size: 23px;
    letter-spacing: 1px;
    color: var(--accent-gold);
    text-transform: uppercase;
  }
  .person-title {
    margin: 6px 0 26px;
    font-family: "Michroma", sans-serif;
    font-size: 16px;
    color: var(--paper-white);
    letter-spacing: 1px;
  }
  .contact-list {
    list-style: none;
    margin: 0;
    padding: 0;
    font-family: "Roboto", Arial, sans-serif;
    font-size: 18px;
    color: var(--paper-white);
  }
  .contact-list li {
    display: flex;
    align-items: center;
    gap: 10px;
    margin-bottom: 9px;
  }
  .contact-icon {
    width: 16px;
    height: 16px;
    flex: none;
  }
</style>
</head>
<body>
<main class="canvas">
  <section class="business-card" aria-label="Business card">
    <svg class="card-swoosh" viewBox="0 0 900 514" aria-hidden="true">
      <path d="M0,338 C300,408 640,428 900,352 L900,386 C620,456 300,432 0,374 Z" fill="var(--paper-white)"/>
      <path d="M0,386 C300,444 620,468 900,398 L900,514 L0,514 Z" fill="var(--accent-gold)"/>
    </svg>

    <h1 class="company-name">
      <span class="line">Bramwell</span>
      <span class="line">Financial</span>
      <span class="line">Advisory Inc.</span>
    </h1>

    <div class="divider"></div>

    <div class="contact-block">
      <p class="person-name">Daniel Whitford</p>
      <p class="person-title">CEO</p>
      <ul class="contact-list">
        <li>
          <svg class="contact-icon" viewBox="0 0 16 16" aria-hidden="true">
            <rect x="3.5" y="1" width="9" height="14" rx="1.5" fill="none" stroke="var(--accent-gold)" stroke-width="2"/>
            <circle cx="8" cy="12.3" r="1" fill="var(--accent-gold)"/>
          </svg>
          044-318 270 546
        </li>
        <li>
          <svg class="contact-icon" viewBox="0 0 16 16" aria-hidden="true">
            <path d="M1,8 L15,1 L10,15 L8,9 Z" fill="var(--accent-gold)"/>
          </svg>
          info@bramwellfa.com
        </li>
        <li>
          <svg class="contact-icon" viewBox="0 0 16 16" aria-hidden="true">
            <circle cx="8" cy="8" r="7" fill="var(--accent-gold)"/>
            <path d="M1,8 H15 M8,1 C5,4 5,12 8,15 M8,1 C11,4 11,12 8,15" fill="none" stroke="var(--card-black)" stroke-width="1.2"/>
          </svg>
          www.bramwellfa.com
        </li>
      </ul>
    </div>
  </section>
</main>
</body>
</html>
```